Business Cards for company that supports physicians that do medical research

Need to create a business card for Qorvel Studies (www.qorvelstudies.example), a company devoted to supporting physicians who conduct medical research. The form of the card should match the message of research and information quest. I have provided the logo of the company as an uploaded file. Designs should be simple and slick aimed at very high end clients.

Target Market(s)

Medical doctors that are also researchers

Industry/Entity Type

Medical

Contact Information for Business Card

Should feature logo and fields for personal info:
Name/title
Phone /email

Font styles to use
Serif
Sans Serif

Requirements
Must have
• Qorvel logo and fields for personal info:
• Name: Bertrand Okonfu
• Title: VP Research and Senior Analyst
• Phone: 555-203-4719
• email: info@qorvelstudies.example
Nice to have
• Interesting cards that I've seen:
• 1- all black/charcoal or very dark background
• 2- Plastic - semi-transparent
• 3- non-standard height-width ratios
• 4- Functional cards -- USB drive incorporated
Should not have
• Too busy; needs to stay very simple

```html
<!DOCTYPE html>
<html lang="en">
<head>
<meta charset="utf-8">
<title>Qorvel Studies — Business Card</title>
<link href="https://fonts.googleapis.com/css2?family=Source+Sans+3:wght@400;600&display=swap" rel="stylesheet">
<style>
  :root {
    --stage-top: #2a2a2a;
    --stage-bottom: #050505;
    --card: #ffffff;
    --green: #5cb947;
    --blue: #1f86c8;
    --ink: #4a4a4a;
  }
  * { box-sizing: border-box; margin: 0; padding: 0; }
  html, body { width: 1200px; height: 900px; overflow: hidden; }
  body {
    position: relative;
    background: linear-gradient(to bottom, var(--stage-top), var(--stage-bottom));
    font-family: "Source Sans 3", "Helvetica Neue", Arial, sans-serif;
  }
  .card {
    position: absolute;
    top: 306px;
    height: 271px;
    background: var(--card);
    border-radius: 10px;
  }
  .card--front { left: 149px; width: 439px; }
  .card--back { left: 608px; width: 441px; height: 272px; }

  .wordmark {
    position: absolute;
    color: var(--green);
    font-weight: 600;
    line-height: 1;
    white-space: nowrap;
  }
  .card--front .wordmark { left: 39px; top: 126px; width: 170px; font-size: 23px; }
  .card--back .wordmark {
    left: 0; right: 0; top: 117px;
    text-align: center; font-size: 36px;
  }

  .holder { position: absolute; left: 227px; top: 96px; color: var(--ink); }
  .holder__name { color: var(--green); font-weight: 600; font-size: 14.5px; line-height: 18px; }
  .holder__title { font-size: 12px; line-height: 15px; }
  .holder__contacts { list-style: none; margin-top: 17px; font-size: 12px; line-height: 16px; }
  .holder__contacts li { display: flex; align-items: center; gap: 5px; }
  .holder__contacts svg { width: 9px; height: 9px; fill: var(--green); }

  .web {
    position: absolute; left: 0; right: 0; top: 219px;
    text-align: center; font-size: 12px; color: var(--blue);
  }
  .web__domain { color: var(--green); }
</style>
</head>
<body>
  <section class="card card--front">
    <div class="wordmark">Qorvel Studies</div>
    <div class="holder">
      <p class="holder__name">Bertrand Okonfu</p>
      <p class="holder__title">VP Research and Senior Analyst</p>
      <ul class="holder__contacts">
        <li>
          <svg viewBox="0 0 10 10" aria-hidden="true"><path d="M1 3c0-1 1-2 4-2s4 1 4 2v1H7V3H3v1H1zM2 5h6l1 4H1z"/></svg>
          555-203-4719
        </li>
        <li>
          <svg viewBox="0 0 10 10" aria-hidden="true"><path d="M1 2h8v6H1z M1 2l4 3 4-3" stroke="#fff" stroke-width="0.8"/></svg>
          info@qorvelstudies.example
        </li>
      </ul>
    </div>
  </section>

  <section class="card card--back">
    <div class="wordmark">Qorvel Studies</div>
    <p class="web">www.<span class="web__domain">qorvelstudies</span>.example</p>
  </section>
</body>
</html>
```